Bourbon label design for bourbon brand. Looking to freshen our current label.

I need a Bourbon label design for our rebranded Bourbon bottle. Label should include picture of our horse and our logo on the bottle. Front Label is 3.5 inches wide and 6 inches tall, back label is 4 inches tall and 3 inches wide. Back label can be a simple plain logo like the one in the brief. I have included a design of our current bottle and label. We want to stay close to the current color schemes but want a fresh rebrand of the design. The label needs to be the correct size on a tall bottle like pictured.

Target Market(s)

Our Bourbon members, 30-50 year old males

Requirements
Must have
• Picture of our horse, our B logo , straight Bourbon whiskey on the front. Room to edit text on the back label.

```html
<!DOCTYPE html>
<html lang="en">
<head>
<meta charset="utf-8">
<title>Nightfall Straight Bourbon Whiskey – Labels</title>
<link href="https://fonts.googleapis.com/css2?family=Oswald:wght@400;500;600;700&family=Mulish:wght@400&display=swap" rel="stylesheet">
<style>
  :root {
    --canvas: #dcdcdc;
    --label-black: #000000;
    --grey-light: #858585;
    --grey-dark: #161616;
    --white: #ffffff;
    --mute: #8c8c8c;
    --shadow: #9a9a9a;
    --photo-light: #b8b8b8;
    --photo-dark: #5a5a5a;
  }
  * { box-sizing: border-box; margin: 0; padding: 0; }
  html, body { width: 1000px; height: 1200px; overflow: hidden; }
  body {
    background: var(--canvas);
    position: relative;
    font-family: "Oswald", "Arial Narrow", sans-serif;
  }
  .label { position: absolute; overflow: hidden; background: var(--label-black); }
  .label__bg { position: absolute; inset: 0; width: 100%; height: 100%; display: block; }
  .label > *:not(.label__bg) { position: absolute; }

  /* Front label */
  .front { left: 88px; top: 81px; width: 329px; height: 562px; }
  .brand-mark {
    left: 16px; top: 44px;
    display: flex; align-items: center; gap: 7px;
    color: var(--label-black); font-weight: 700; font-size: 25px; line-height: 1;
    letter-spacing: 0.5px;
  }
  .brand-mark__square { width: 14px; height: 14px; background: var(--label-black); }
  .class-stack {
    right: 28px; top: 38px; text-align: right;
    color: var(--white); font-weight: 500; font-size: 18px; line-height: 24px;
    letter-spacing: 0.4px;
  }
  .horse-photo {
    left: 109px; top: 130px; width: 126px; height: 240px;
    background: linear-gradient(180deg, var(--photo-light), var(--photo-dark));
    border-radius: 40px 40px 20px 20px;
  }
  .est-rule { left: 58px; width: 213px; height: 1px; background: var(--white); }
  .est-rule--top { top: 312px; }
  .est-rule--bottom { top: 344px; }
  .est-year {
    left: 58px; top: 318px; width: 213px;
    display: flex; justify-content: space-between;
    color: var(--white); font-weight: 500; font-size: 15px; line-height: 20px;
  }
  .product-name {
    left: 0; top: 368px; width: 100%; text-align: center;
    color: var(--white); font-weight: 700; font-size: 62px; line-height: 64px;
    letter-spacing: 0.5px;
    text-shadow: 3px 3px 0 var(--shadow);
  }
  .expression {
    left: 0; top: 441px; width: 100%; text-align: center;
    color: var(--white); font-weight: 500; font-size: 15px; line-height: 20px;
    letter-spacing: 0.5px;
  }
  .fill-fields {
    left: 0; top: 517px; width: 100%;
    color: var(--mute); font-weight: 500; font-size: 11px; line-height: 14px;
  }
  .fill-fields span { position: absolute; transform: translateX(-50%); white-space: nowrap; }
  .front__foot { left: 0; bottom: 0; width: 100%; height: 25px; background: var(--white); }

  /* Back label */
  .back { left: 108px; top: 746px; width: 285px; height: 377px; }
  .back .brand-mark {
    left: 0; top: 52px; width: 100%; justify-content: center; font-size: 24px;
  }
  .back__name {
    left: 0; top: 132px; width: 100%; text-align: center;
    color: var(--white); font-weight: 700; font-size: 29px; line-height: 30px;
    text-shadow: 2px 2px 0 var(--shadow);
  }
  .back__class {
    left: 0; top: 164px; width: 100%; text-align: center;
    color: var(--white); font-weight: 500; font-size: 13px; line-height: 16px;
    letter-spacing: 0.3px;
  }
  .back__copy {
    left: 31px; top: 191px; width: 223px; text-align: center;
    color: var(--white); font-family: "Mulish", "Helvetica", sans-serif;
    font-size: 10.4px; line-height: 13.3px;
  }
</style>
</head>
<body>

<section class="label front" aria-label="Front label">
  <svg class="label__bg" viewBox="0 0 329 562" preserveAspectRatio="none" aria-hidden="true">
    <defs>
      <linearGradient id="frontShade" x1="0" y1="0" x2="0" y2="1">
        <stop offset="0" stop-color="#858585"/>
        <stop offset="1" stop-color="#161616"/>
      </linearGradient>
    </defs>
    <rect width="329" height="562" fill="#000"/>
    <polygon points="0,0 329,0 329,205 0,376" fill="url(#frontShade)"/>
  </svg>

  <div class="brand-mark"><span class="brand-mark__square"></span>BARROW RIDGE</div>

  <p class="class-stack">STRAIGHT<br>BOURBON<br>WHISKEY</p>

  <div class="horse-photo" role="img" aria-label="Black and white photo of the racehorse and jockey galloping toward the viewer"></div>

  <div class="est-rule est-rule--top"></div>
  <p class="est-year"><span>EST.</span><span>2016</span></p>
  <div class="est-rule est-rule--bottom"></div>

  <h1 class="product-name">NIGHTFALL</h1>
  <p class="expression">SINGLE BARREL | BARREL STRENGTH</p>

  <div class="fill-fields">
    <span style="left:48px">BARREL NO.</span>
    <span style="left:168px">AGED/YEARS</span>
    <span style="left:282px">ALC./VOL.</span>
  </div>

  <div class="front__foot"></div>
</section>

<section class="label back" aria-label="Back label">
  <svg class="label__bg" viewBox="0 0 285 377" preserveAspectRatio="none" aria-hidden="true">
    <defs>
      <linearGradient id="backShade" x1="0" y1="0" x2="0" y2="1">
        <stop offset="0" stop-color="#858585"/>
        <stop offset="1" stop-color="#161616"/>
      </linearGradient>
    </defs>
    <rect width="285" height="377" fill="#000"/>
    <polygon points="0,0 285,0 285,128 0,305" fill="url(#backShade)"/>
  </svg>

  <div class="brand-mark"><span class="brand-mark__square"></span>BARROW RIDGE</div>

  <h2 class="back__name">NIGHTFALL</h2>
  <p class="back__class">STRAIGHT BOURBON WHISKEY</p>

  <p class="back__copy">Lorem ipsum dolor sit amet, consectetur adipiscing elit. Quisque placerat sem at nunc venenatis venenatis. Vestibulum dapibus dui lectus, non accumsan mauris tincidunt et. In non viverra turpis. Aenean id finibus magna, et feugiat ipsum. Proin laoreet gravida lorem nec porta. Suspendisse a neque dictum, tempus lorem ac, suscipit dolor. Fusce id eleifend dolor. Quisque rhoncus sem vel tortor dapibus accumsan.</p>
</section>

</body>
</html>
```